Business card for medical clinic

I need an upmarket, modern medical/health business card for my clinic

Contact Information for Business Card

name, address, email, qr code

```html
<!DOCTYPE html>
<html lang="en">
<head>
<meta charset="utf-8">
<title>Northvale Health – Business Card</title>
<link href="https://fonts.googleapis.com/css2?family=Cinzel:wght@500&family=Merriweather:wght@300&display=swap" rel="stylesheet">
<style>
  :root {
    --backdrop: #d3d4d6;
    --navy: #2b2e45;
    --sky: #2fb3e6;
    --brand-blue: #1f6fa8;
    --ink: #2a2a2a;
    --rule: #1d3a66;
    --white: #ffffff;
  }
  html, body {
    margin: 0;
    padding: 0;
    width: 900px;
    height: 1200px;
    overflow: hidden;
    background: var(--backdrop);
  }
  .card {
    position: absolute;
    left: 133px;
    width: 633px;
    height: 364px;
    overflow: hidden;
  }
  .card--front {
    top: 210px;
    background: linear-gradient(180deg, var(--navy) 0%, #33466a 35%, #3d86ad 65%, var(--sky) 100%);
  }
  .card--back {
    top: 624px;
    background: var(--white);
  }
  .brand {
    position: absolute;
    display: flex;
    align-items: center;
    white-space: nowrap;
  }
  .brand-ring {
    flex: none;
    border-radius: 50%;
    box-sizing: border-box;
  }
  .brand-name {
    font-family: "Cinzel", serif;
    font-weight: 500;
    letter-spacing: 1px;
    margin: 0;
    line-height: 1;
  }
  .card--front .brand {
    left: 137px; top: 158px; height: 50px; gap: 14px;
  }
  .card--front .brand-ring {
    width: 50px; height: 50px;
    border: 3px solid var(--white);
  }
  .card--front .brand-name {
    font-size: 27px;
    color: var(--white);
  }
  .card--back .brand {
    left: 32px; top: 164px; height: 36px; gap: 10px;
  }
  .card--back .brand-ring {
    width: 36px; height: 36px;
    border: 3px solid var(--brand-blue);
  }
  .card--back .brand-name {
    font-size: 20px;
    color: var(--brand-blue);
  }
  .divider {
    position: absolute;
    left: 316px; top: 94px;
    width: 2px; height: 178px;
    background: linear-gradient(180deg, var(--rule), var(--sky));
  }
  .contact {
    position: absolute;
    left: 330px; top: 90px;
    font-family: "Merriweather", serif;
    font-weight: 300;
    color: var(--ink);
    font-size: 15px;
  }
  .contact__name {
    font-family: "Cinzel", serif;
    font-weight: 500;
    font-size: 22px;
    color: var(--brand-blue);
    margin: 0;
    line-height: 1;
    letter-spacing: 0.5px;
  }
  .contact__role { margin: 6px 0 0; }
  .contact__address { margin: 14px 0 0; line-height: 22px; font-style: normal; }
  .contact__list { list-style: none; padding: 0; margin: 10px 0 0; }
  .contact__list li { display: flex; align-items: center; gap: 6px; height: 25px; }
  .contact__list svg { width: 12px; height: 12px; flex: none; }
  .phone-number { letter-spacing: 2.5px; }
</style>
</head>
<body>
  <section class="card card--front">
    <div class="brand">
      <span class="brand-ring"></span>
      <h1 class="brand-name">Northvale Health</h1>
    </div>
  </section>

  <section class="card card--back">
    <div class="brand">
      <span class="brand-ring"></span>
      <p class="brand-name">Northvale Health</p>
    </div>
    <span class="divider"></span>
    <div class="contact">
      <h2 class="contact__name">DANIEL HARROW</h2>
      <p class="contact__role">Principal Consultant</p>
      <address class="contact__address">PO Box 480215<br>Birch Creek, Oregon 97031</address>
      <ul class="contact__list">
        <li>
          <svg viewBox="0 0 24 24" aria-hidden="true"><path fill="#1f6fa8" d="M6.6 10.8a15.1 15.1 0 0 0 6.6 6.6l2.2-2.2c.3-.3.7-.4 1-.2 1.1.4 2.3.6 3.6.6.6 0 1 .4 1 1V20c0 .6-.4 1-1 1A17 17 0 0 1 3 4c0-.6.4-1 1-1h3.5c.6 0 1 .4 1 1 0 1.3.2 2.5.6 3.6.1.3 0 .7-.2 1z"/></svg>
          <span class="phone-number">+1-555-214-0937</span>
        </li>
        <li>
          <svg viewBox="0 0 24 24" aria-hidden="true"><rect x="2" y="5" width="20" height="14" fill="#1f6fa8"/><path d="M2 5l10 8 10-8" fill="none" stroke="#fff" stroke-width="1.5"/></svg>
          <span>info@northvalehealthpartners.com</span>
        </li>
        <li>
          <svg viewBox="0 0 24 24" aria-hidden="true"><g fill="none" stroke="#1f6fa8" stroke-width="2"><circle cx="12" cy="12" r="10"/><ellipse cx="12" cy="12" rx="4" ry="10"/><path d="M2 12h20M4 7h16M4 17h16"/></g></svg>
          <span>www.northvalehealthpartners.com</span>
        </li>
      </ul>
    </div>
  </section>
</body>
</html>
```